BOLD & MINIMALIST DESIGN NEEDED

We want a very bold but minimalistic business card design that is impactful and utilizes both sides of the business card. Our current logo is included for your use.

We want bold fonts and good use of negative space. We don't want the logo to overpower the design.

Target Market(s)

Professionals who are building new commercial buildings.

Industry/Entity Type

Construction

Contact Information for Business Card

Name, Title, email, office phone, cell phone, website

Font styles to use
Serif
Sans Serif

Requirements
Must have
• Bold design!

```html
<!DOCTYPE html>
<html lang="en">
<head>
<meta charset="utf-8">
<title>Ridgeline Build Co. — Business Card</title>
<link rel="stylesheet" href="https://fonts.googleapis.com/css2?family=Poppins:wght@400;500;600;700&display=swap">
<style>
  :root {
    --page-bg: #d9d4ce;
    --card-top: #f1efec;
    --card-bottom: #dcd8d3;
    --charcoal: #231f20;
    --brand-green: #6fb42c;
    --contact-text: #d8c9b4;
    --title-text: #2a2a2a;
  }
  html, body {
    margin: 0;
    padding: 0;
    width: 1200px;
    height: 1054px;
    overflow: hidden;
    background: var(--page-bg);
    font-family: "Poppins", sans-serif;
  }
  .business-card {
    position: absolute;
    left: 100px;
    top: 227px;
    width: 1000px;
    height: 600px;
    border-radius: 26px;
    overflow: hidden;
    background: linear-gradient(180deg, var(--card-top), var(--card-bottom));
    box-shadow: 0 18px 40px rgba(0,0,0,0.18);
  }
  .card-waves {
    position: absolute;
    inset: 0;
    width: 100%;
    height: 100%;
  }
  .brand-name {
    position: absolute;
    left: 92px;
    top: 228px;
    display: flex;
    align-items: center;
    gap: 16px;
    font-weight: 700;
    font-size: 46px;
    color: var(--charcoal);
    letter-spacing: 1px;
  }
  .brand-square {
    width: 40px;
    height: 40px;
    background: var(--brand-green);
  }
  .person {
    position: absolute;
    right: 58px;
    top: 60px;
    text-align: right;
  }
  .person-name {
    margin: 0;
    font-weight: 600;
    font-size: 42px;
    line-height: 1.1;
    color: var(--brand-green);
  }
  .person-title {
    margin: 8px 0 0;
    font-weight: 400;
    font-size: 23px;
    color: var(--title-text);
  }
  .contact-list {
    position: absolute;
    right: 58px;
    top: 432px;
    margin: 0;
    padding: 0;
    list-style: none;
    text-align: right;
  }
  .contact-item {
    display: flex;
    justify-content: flex-end;
    align-items: center;
    gap: 14px;
    font-size: 24px;
    line-height: 35px;
    color: var(--contact-text);
  }
  .contact-icon {
    width: 20px;
    height: 20px;
    flex: none;
  }
</style>
</head>
<body>
  <div class="business-card">
    <svg class="card-waves" viewBox="0 0 1000 600" preserveAspectRatio="none" aria-hidden="true">
      <path fill="var(--charcoal)" d="M0,555 C180,575 400,545 590,430 C720,350 860,345 1000,350 L1000,600 L0,600 Z"/>
      <path fill="var(--brand-green)" d="M0,470 C120,520 300,540 470,460 C640,380 780,315 1000,318 L1000,336 C800,332 660,395 500,470 C330,548 140,540 0,500 Z"/>
      <path fill="var(--brand-green)" d="M80,510 C250,545 420,520 560,450 C470,510 300,560 80,510 Z" opacity="0.9"/>
    </svg>

    <div class="brand-name"><span class="brand-square"></span>RIDGELINE BUILD CO.</div>

    <div class="person">
      <p class="person-name">Daniel Reyes</p>
      <p class="person-title">Director</p>
    </div>

    <ul class="contact-list">
      <li class="contact-item">555-014-0192
        <svg class="contact-icon" viewBox="0 0 20 20"><path fill="var(--brand-green)" d="M2 6c0-2 2-3 8-3s8 1 8 3v1h-4V5.5H6V7H2zM5 9l2-2h6l2 2 2 6v2H3v-2zM10 10a2.5 2.5 0 1 0 0 5a2.5 2.5 0 1 0 0-5z"/></svg>
      </li>
      <li class="contact-item">dan@ridgelinebuild.com
        <svg class="contact-icon" viewBox="0 0 20 20"><rect x="2" y="4" width="16" height="12" fill="var(--brand-green)"/><path d="M2 4l8 7 8-7" fill="none" stroke="var(--charcoal)" stroke-width="1.5"/></svg>
      </li>
      <li class="contact-item">www.ridgelinebuild.com
        <svg class="contact-icon" viewBox="0 0 20 20"><circle cx="10" cy="10" r="8" fill="var(--brand-green)"/><path d="M2 10h16M10 2c-4 4-4 12 0 16M10 2c4 4 4 12 0 16" fill="none" stroke="var(--charcoal)" stroke-width="1.2"/></svg>
      </li>
    </ul>
  </div>
</body>
</html>
```